Photographer's price list

I am a photographer who runs a studio (Marrowfield Studio) and need to have a document to send clients detailing my packages (collections) and prices. I have written the text in a word document and need a designer to lay it out for me using my logo and two specific fonts: DejaVu Sans and LainieDaySH.

The look should be clean and modern and keep in the same style as my logo. I will primarily be using the final product as a PDF file to email to potential clients. It should stay black and white.

I would also like to be able to update the text myself as my prices and packages change. So I would like a PSD file.

I think I would like for the document to be in landscape format with "Collections" on one side and A la Carte on the other, but I am open to other ideas.

As for sizing, it should be a standard size so that clients can print it out if they like.

Industry/Entity Type

Landscape

Requirements
Must have
• my logo
fonts: DejaVu and LainieDaySH
Easy to email
Easy to display on one page upon opening
Standard size so that printing from a home computer is easy to do.

```html
<!DOCTYPE html>
<html lang="en">
<head>
<meta charset="utf-8">
<title>Marrowfield Studio – 2013 Photography Collections</title>
<link href="https://fonts.googleapis.com/css2?family=Allura&family=Noto+Sans:wght@400;700&display=swap" rel="stylesheet">
<style>
  :root{
    --page:#ffffff;
    --panel:#252525;
    --band:#777777;
    --card:#353333;
    --text-light:#e4e4e4;
    --text-mid:#bdbdbd;
    --text-dim:#6e6e6e;
    --ribbon-a:#f2f2f2;
    --ribbon-b:#8a8a8a;
    --photo-a:#d9d9d9;
    --photo-b:#8c8c8c;
  }
  *{margin:0;padding:0;box-sizing:border-box}
  html,body{width:775px;height:1200px;overflow:hidden;background:var(--page)}
  body{position:relative;font-family:"Noto Sans",sans-serif;color:var(--text-light)}
  .script{font-family:"Allura",cursive;font-weight:400}

  /* cover panel */
  .cover{position:absolute;left:17px;top:19px;width:741px;height:571px;background:var(--panel);overflow:hidden}
  .cover-accent{position:absolute;left:336px;top:0;width:35px;height:172px;background:var(--band)}
  .cover-photo{position:absolute;left:371px;top:0;width:370px;height:172px;
    background:linear-gradient(120deg,var(--photo-a),#b4b4b4 45%,var(--photo-b))}
  .cover-band{position:absolute;left:0;bottom:0;width:100%;height:64px;background:var(--band)}
  .studio-mark{position:absolute;left:543px;top:196px;width:154px;height:154px}
  .studio-name{position:absolute;left:543px;top:260px;width:154px;text-align:center;
    font-size:11.5px;letter-spacing:1.4px;color:var(--panel);font-weight:400}
  .cover-year{position:absolute;right:58px;top:400px;font-size:44px;color:var(--text-mid)}
  .cover-title{position:absolute;right:22px;top:450px;font-size:40px;color:var(--text-light)}
  .contact{position:absolute;left:102px;top:437px;width:200px;text-align:center;font-size:9.5px;line-height:12px;color:var(--text-dim)}
  .contact strong{display:block;font-weight:700}

  /* price panel */
  .prices{position:absolute;left:17px;top:612px;width:741px;height:574px;background:var(--panel)}
  .collection{position:absolute;left:30px;width:311px;height:93px;background:var(--card);border-radius:9px}
  .collection .ribbon{position:absolute;left:-4px;top:0;width:110px;height:50px}
  .collection h2{position:absolute;left:0;width:100%;top:3px;text-align:center;font-size:27px;line-height:30px;color:var(--text-light);padding-left:50px}
  .collection p{position:absolute;left:0;top:30px;width:100%;text-align:center;font-size:8.8px;line-height:11px;padding:0 8px}
  .includes{position:absolute;left:30px;top:468px;width:311px;text-align:center}
  .includes h3{font-size:20px;color:var(--text-mid);line-height:22px}
  .includes p{font-size:7.5px;line-height:9.5px;color:var(--text-mid);margin-top:2px}

  .carte{position:absolute;left:380px;width:340px;text-align:center}
  .carte h3{font-size:20px;line-height:22px;color:var(--text-mid);margin-bottom:2px}
  .carte p{font-size:9px;line-height:10.6px;color:var(--text-light)}
  .price{color:var(--text-dim)}
</style>
</head>
<body>

<section class="cover">
  <div class="cover-accent"></div>
  <div class="cover-photo" role="img" aria-label="Black and white family portrait with parents, two young daughters and a newborn"></div>
  <svg class="studio-mark" viewBox="0 0 154 154" aria-hidden="true">
    <circle cx="77" cy="77" r="77" fill="#ffffff"/>
  </svg>
  <div class="studio-name">MARROWFIELD STUDIO</div>
  <div class="cover-year script">2013</div>
  <div class="cover-title script">photography collections</div>
  <div class="contact">
    <strong>Contact Information</strong>
    Clara Wendt<br>+49 155 000 4812<br>Lindenau, 04177<br>Germany
  </div>
  <div class="cover-band"></div>
</section>

<section class="prices">
  <article class="collection" style="top:35px">
    <svg class="ribbon" viewBox="0 0 110 50" aria-hidden="true">
      <defs><linearGradient id="rb" x1="0" y1="0" x2="1" y2="0"><stop offset="0" stop-color="var(--ribbon-a)"/><stop offset="1" stop-color="var(--ribbon-b)" stop-opacity="0"/></linearGradient></defs>
      <polygon points="0,34 90,0 110,0 0,46" fill="url(#rb)"/>
      <text x="22" y="33" transform="rotate(-21 22 33)" font-family="Noto Sans,sans-serif" font-weight="700" font-size="11" fill="#2a2a2a">300 €</text>
    </svg>
    <h2 class="script">Collection 1</h2>
    <p>Your favorite five images from the session will be<br>professionally edited and presented to you on disk as<br>high resolution jpegs</p>
  </article>

  <article class="collection" style="top:141px">
    <svg class="ribbon" viewBox="0 0 110 50" aria-hidden="true">
      <polygon points="0,34 90,0 110,0 0,46" fill="url(#rb)"/>
      <text x="22" y="33" transform="rotate(-21 22 33)" font-family="Noto Sans,sans-serif" font-weight="700" font-size="11" fill="#2a2a2a">400 €</text>
    </svg>
    <h2 class="script">Collection 2</h2>
    <p>Your favorite ten images from the session will be<br>professionally edited and given to you on disk as<br>high resolution jpegs.<br>Your favorite image from the session will be<br>professionally printed for you (20x30cm) on Arlenbach paper,<br>Clara's favorite for portraits.</p>
  </article>

  <article class="collection" style="top:249px">
    <svg class="ribbon" viewBox="0 0 110 50" aria-hidden="true">
      <polygon points="0,34 90,0 110,0 0,46" fill="url(#rb)"/>
      <text x="22" y="33" transform="rotate(-21 22 33)" font-family="Noto Sans,sans-serif" font-weight="700" font-size="11" fill="#2a2a2a">500 €</text>
    </svg>
    <h2 class="script">Collection 3</h2>
    <p>Your favorite <u>fifteen</u> images from the session will be<br>professionally edited and presented to you on disk as<br>high resolution jpegs.<br>Your favorite <u>two</u> images from the session will be<br>professionally printed for you (20x30cm) on Arlenbach paper,<br>Clara's favorite for portraits.</p>
  </article>

  <article class="collection" style="top:356px">
    <svg class="ribbon" viewBox="0 0 110 50" aria-hidden="true">
      <polygon points="0,34 90,0 110,0 0,46" fill="url(#rb)"/>
      <text x="22" y="33" transform="rotate(-21 22 33)" font-family="Noto Sans,sans-serif" font-weight="700" font-size="11" fill="#2a2a2a">600 €</text>
    </svg>
    <h2 class="script">Collection 4</h2>
    <p><u>ALL</u> presented images from the session will be<br>professionally edited and presented to you on disk as<br>high resolution jpegs (approximately 40+ images).<br>Your favorite <u>two</u> images from the session will be<br>professionally printed for you (20x30cm) on Arlenbach paper,<br>Clara's favorite for portraits.</p>
  </article>

  <div class="includes">
    <h3 class="script">all collections include:</h3>
    <p>One to two hour portrait session with photographer in location<br>of your choice (unlimited time if necessary!)<br>Clara will create a presentation video with hand-selected<br>music and custom editing, which tells your story,<br>highlights the best images, and reveals the connections within<br>your family.<br>An online gallery for viewing and ordering<br>helps you share your images with family and friends.</p>
  </div>

  <div class="carte" style="top:28px">
    <h3 class="script">a la carte pricing</h3>
    <p>These products may be purchased separately to complement<br>your collection. A consultation with Clara will help you decide<br>which products are best for gifts and for your home.</p>
  </div>
  <div class="carte" style="top:111px">
    <h3 class="script">high resolution digital images</h3>
    <p>Perfect if you just need to add "one more image" to your<br>collection!<br>High-resolution jpeg file <span class="price">25 €</span> each</p>
  </div>
  <div class="carte" style="top:179px">
    <h3 class="script">matt prints</h3>
    <p>20x30 cm and smaller <span class="price">45 €</span><br>Each print is professionally edited, printed on archival photo<br>paper.<br>Purchase includes the JPEG file for your personal digital use.</p>
  </div>
  <div class="carte" style="top:257px">
    <h3 class="script">arlenbach prints</h3>
    <p>Prints on Arlenbach (watercolor) paper are Clara's favorite for<br>large format color prints<br>30x40 cm <span class="price">95 €</span></p>
  </div>
  <div class="carte" style="top:329px">
    <h3 class="script">canvas prints</h3>
    <p>Ready-to-hang, stretched canvas wall art of your favorite images<br>30x40 cm <span class="price">150 €</span></p>
  </div>
  <div class="carte" style="top:388px">
    <h3 class="script">framed + matted prints</h3>
    <p>Beautiful Arlenbach prints finished with wide mats and simple,<br>elegant frames of your choice<br>30x40 inch <span class="price">175 €</span></p>
  </div>
  <div class="carte" style="top:458px">
    <h3 class="script">custom designed albums</h3>
    <p>Images from your session are selected for the custom design of<br>an album and bound in a book for a modern presentation of your<br>images. There are a number of cover choices for the classic<br>flush-mount and beautifully crafted albums. A great way to<br>display all of your favorite images from your session on your<br>coffee table.<br>Prices begin at <span class="price">500 €</span></p>
  </div>
</section>

</body>
</html>
```